Modern business card design for professional copywriter

I'd like a business card design that I can use to have my cards printed out by quillprint.com as a squared corners business card (see artwork and design guidelines here: https://help.quillprint.com/hc/en-gb/sections/200570950-QUILL-Product-Templates)

The design should be clean and modern and reflect the colours, tone and branding on my website: https://tessavorrin.com.au

Target Market(s)

Professionals, B2B small business owners

Industry/Entity Type

Business

Contact Information for Business Card

Tessa Vorrin
m: 0468 905 327
e: tessa@tessavorrin.com.au
w: tessavorrin.com.au

Font styles to use
Sans Serif

Requirements
Must have
• Tagline: "Smart copywriting for clever business people"
• Brand colours: fd8000, 009984, 666666 and black
Nice to have

```html
<!DOCTYPE html>
<html lang="en">
<head>
<meta charset="utf-8">
<title>Tessa Vorrin — Copywriter Business Card</title>
<link rel="stylesheet" href="https://fonts.googleapis.com/css2?family=Lato:wght@400;700;900&display=swap">
<style>
  :root {
    --orange: #f7862a;
    --orange-deep: #ec7420;
    --orange-light: #fb9440;
    --teal: #009984;
    --grey: #666666;
    --ink: #111111;
    --paper: #ffffff;
    --backdrop: #ececec;
  }
  * { box-sizing: border-box; margin: 0; padding: 0; }
  html, body { width: 1200px; height: 586px; overflow: hidden; }
  body {
    background: var(--backdrop);
    font-family: "Lato", Arial, sans-serif;
    position: relative;
  }
  .card {
    position: absolute;
    top: 129px;
    width: 502px;
    height: 301px;
    overflow: hidden;
  }
  .card--front { left: 62px; }
  .card--back { left: 619px; background: var(--paper); }

  .front-pattern {
    position: absolute; inset: 0;
    background: linear-gradient(135deg, var(--orange-light) 0%, var(--orange) 45%, var(--orange-deep) 100%);
  }
  .front-brand {
    position: absolute; left: 0; right: 0; top: 118px;
    text-align: center; color: var(--paper);
  }
  .brand-name {
    font-weight: 400;
    font-size: 50px;
    line-height: 1;
    letter-spacing: -0.5px;
  }
  .brand-role {
    margin-top: 6px;
    font-size: 14px;
    letter-spacing: 7px;
    text-transform: uppercase;
  }

  .back-brand {
    position: absolute; left: 0; right: 0; top: 36px;
    text-align: center;
  }
  .back-brand .brand-name { font-size: 38px; color: var(--orange); }
  .back-brand .brand-role { font-size: 11px; letter-spacing: 5px; color: var(--grey); margin-top: 4px; }

  .services {
    position: absolute; right: 273px; top: 149px;
    list-style: none; text-align: right;
    font-weight: 900; font-size: 10.5px; color: var(--ink);
    line-height: 18.5px; white-space: nowrap;
  }
  .divider { position: absolute; left: 244px; top: 143px; }

  .contact { position: absolute; left: 270px; top: 161px; }
  .social { display: flex; gap: 8px; margin-bottom: 8px; }
  .social span {
    width: 19px; height: 19px; border-radius: 50%; background: var(--orange);
  }
  .contact-row {
    display: flex; align-items: center; gap: 7px;
    font-size: 12px; color: var(--ink); height: 24px;
  }
  .contact-row svg { flex: none; }
  .website {
    margin-top: 3px;
    font-weight: 900; font-size: 12px; letter-spacing: 1px; color: var(--teal);
  }
</style>
</head>
<body>
  <section class="card card--front">
    <div class="front-pattern" role="img" aria-label="Faceted low-poly orange geometric background pattern"></div>
    <div class="front-brand">
      <div class="brand-name">Tessa Vorrin</div>
      <div class="brand-role">Copywriter</div>
    </div>
  </section>

  <section class="card card--back">
    <div class="back-brand">
      <div class="brand-name">Tessa Vorrin</div>
      <div class="brand-role">Copywriter</div>
    </div>

    <ul class="services">
      <li>Feature Writing</li>
      <li>SEO Copywriting</li>
      <li>Legal Copywriting</li>
      <li>Content Marketing</li>
      <li>Website Copywriting</li>
      <li>Small Business Copywriting</li>
    </ul>

    <svg class="divider" width="8" height="124" viewBox="0 0 8 124" aria-hidden="true">
      <g fill="#f7862a">
        <circle cx="4" cy="4" r="3"/><circle cx="4" cy="16" r="3"/><circle cx="4" cy="28" r="3"/>
        <circle cx="4" cy="40" r="3"/><circle cx="4" cy="52" r="3"/><circle cx="4" cy="64" r="3"/>
        <circle cx="4" cy="76" r="3"/><circle cx="4" cy="88" r="3"/><circle cx="4" cy="100" r="3"/>
        <circle cx="4" cy="112" r="3"/><circle cx="4" cy="120" r="3"/>
      </g>
    </svg>

    <div class="contact">
      <div class="social" aria-label="Social profiles">
        <span></span><span></span><span></span><span></span>
      </div>
      <div class="contact-row">
        <svg width="18" height="18" viewBox="0 0 18 18" aria-hidden="true">
          <circle cx="9" cy="9" r="9" fill="#009984"/>
          <path d="M5 7.5 Q9 4.5 13 7.5 L12 9 L10.5 8.2 L10.5 7.4 L7.5 7.4 L7.5 8.2 L6 9 Z M6.5 10 H11.5 L12.5 13 H5.5 Z" fill="#fff"/>
        </svg>
        <span>0468 905 327</span>
      </div>
      <div class="contact-row">
        <svg width="18" height="18" viewBox="0 0 18 18" aria-hidden="true">
          <circle cx="9" cy="9" r="9" fill="#009984"/>
          <rect x="4.5" y="6" width="9" height="6.5" fill="#fff"/>
          <path d="M4.5 6 L9 9.8 L13.5 6" fill="none" stroke="#009984" stroke-width="1"/>
        </svg>
        <span>tessa@tessavorrin.com.au</span>
      </div>
      <div class="website">www.tessavorrin.com.au</div>
    </div>
  </section>
</body>
</html>
```